Destination PDF Template (Editable)

Objective: Create a visually stunning and compelling PDF brochure that showcases The Vorelka Crest Lodge as the ultimate luxury hunting destination in Kyrgyzstan, specializing in Marco Polo and Ibex hunts. The PDF should evoke a sense of exclusivity, adventure, and the breathtaking beauty of the Tian Shan mountains, ultimately driving bookings.
Target Audience: High-net-worth individuals, discerning hunters seeking exceptional experiences, adventure travelers, and those interested in unique and luxurious wilderness experiences.
Overall Tone & Style: Sophisticated, elegant, and aspirational. Think high-end travel magazines combined with a touch of rugged adventure. Avoid anything that feels generic or overly commercial. The design should reflect the unparalleled nature of the lodge and the hunts offered. (I'm attaching a reference PDF that i like), as well as another instructions file. Drive link for photos: https://files.pondery-share.net/box/folders/7KqLm2xVbR4tWz9hN3cJpE6yF0aDs8uG?mode=open
Another Link: https://files.pondery-share.net/box/u/0/folders/9ZtRe4wQmN2bVx7kLp5sHc8jYd3fGa1oU

```html
<!DOCTYPE html>
<html lang="en">
<head>
<meta charset="utf-8">
<title>The Adventures — The Vorelka Crest Lodge</title>
<link rel="stylesheet" href="https://fonts.googleapis.com/css2?family=Mrs+Saint+Delafield&family=Poppins:wght@300&display=swap">
<style>
  :root {
    --paper: #f7f7f5;
    --ink-navy: #1d2840;
    --ink-body: #3b3b3d;
    --tone-mountain: #8a7a62;
    --tone-range: #a79a82;
    --tone-sky: #b9cde0;
    --tone-snow: #e9ecef;
    --tone-ridge: #7c7468;
  }
  * { margin: 0; padding: 0; box-sizing: border-box; }
  html, body { width: 1200px; height: 675px; overflow: hidden; }
  body { background: var(--paper); }

  .spread {
    position: relative;
    width: 1200px;
    height: 675px;
    background:
      repeating-linear-gradient(135deg, rgba(0,0,0,0.012) 0 2px, transparent 2px 5px),
      var(--paper);
    overflow: hidden;
  }

  .section-title {
    position: absolute;
    left: 106px;
    top: 158px;
    font-family: "Mrs Saint Delafield", cursive;
    font-weight: 400;
    font-size: 104px;
    line-height: 1;
    color: var(--ink-navy);
    white-space: nowrap;
  }

  .section-intro {
    position: absolute;
    left: 111px;
    top: 292px;
    width: 430px;
    font-family: "Poppins", sans-serif;
    font-weight: 300;
    font-size: 22.5px;
    line-height: 39px;
    color: var(--ink-body);
  }

  .photo {
    position: absolute;
    display: block;
  }
  .photo--horseback {
    left: 599px; top: 31px; width: 302px; height: 349px;
    background: linear-gradient(170deg, #6f6457 0%, var(--tone-mountain) 50%, #b39669 100%);
  }
  .photo--group {
    left: 778px; top: 269px; width: 276px; height: 337px;
    background: linear-gradient(180deg, #a9adb1 0%, #7d7567 45%, var(--tone-ridge) 100%);
  }
  .photo--marksman {
    left: 894px; top: 89px; width: 283px; height: 230px;
    background: linear-gradient(180deg, var(--tone-range) 0%, #b6a27c 45%, #8f8577 100%);
  }
  .photo--trophy {
    left: 556px; top: 379px; width: 246px; height: 200px;
    background: linear-gradient(180deg, var(--tone-sky) 0%, #9fb3c4 55%, var(--tone-snow) 100%);
  }
</style>
</head>
<body>
  <main class="spread">
    <h1 class="section-title">The Adventures</h1>
    <p class="section-intro">A horseback ride you’ll never forget. Challenging hunts for prized game. A stunning camp to revitalize your spirit. This is the hunt of a lifetime.</p>

    <div class="photo photo--horseback" role="img" aria-label="Hunter on a white horse on a rocky mountain slope, pointing ahead beside a guide"></div>
    <div class="photo photo--group" role="img" aria-label="Hunting party in camouflage posing with horses on a rocky mountainside"></div>
    <div class="photo photo--marksman" role="img" aria-label="Hunter lying prone aiming a scoped rifle on a blanket in a dry highland valley"></div>
    <div class="photo photo--trophy" role="img" aria-label="Smiling hunter in winter gear kneeling behind a Marco Polo ram trophy on a snowy ridge"></div>
  </main>
</body>
</html>
```